need corporate, modern business card created for Consulting Company

I need a slick business card using elements from my website, as well as, integrating my pixelforge-created logo (see files).

The business card needs to be:
1. Corporate and modern
2. Clean and professional

I've included a PSD with the logo/icon that you can use to create it. Feel free to try a metallic finish on the logo, make it bigger/small, underlay it. Whatever you need to do to make my card stand out.

Try a black background, or white background or gray.

The idea is for my card to be memorable as well as professional and corporate.

Target Market(s)

Corporate business in the US and Canada.

Industry/Entity Type

Business

Contact Information for Business Card

Commerce Advancing Methods
Martin Coles, Senior Partner
office: 1 877 555 0143
mobile: 1 519 555 0172
website: http://www.brightvale.example

Requirements
Must have
• Card-related information
• corporate, yet modern
• clean and professional
• incorporate the icon only
• must have an editable form when complete!
Nice to have
• metallic icon might be cool
• try it with white or black

```html
<!DOCTYPE html>
<html lang="en">
<head>
<meta charset="utf-8">
<title>Commerce Advancing Methods — Business Card</title>
<link rel="stylesheet" href="https://fonts.googleapis.com/css2?family=PT+Sans:ital,wght@0,400;0,700;1,700&family=PT+Sans+Narrow:wght@700&display=swap">
<style>
  :root {
    --stage: #9a9a9a;
    --stage-light: #d9d9d9;
    --card-black: #111214;
    --card-black-2: #1c1d20;
    --accent-blue: #0f5db8;
    --accent-blue-dark: #0a3f80;
    --silver: #d6dbe0;
    --silver-edge: #5fa6d6;
    --name-blue: #1a5fb4;
  }
  * { margin: 0; padding: 0; box-sizing: border-box; }
  html, body { width: 1200px; height: 900px; overflow: hidden; }
  body {
    background: radial-gradient(ellipse at 50% 45%, var(--stage-light), var(--stage) 80%);
    font-family: "PT Sans", Arial, sans-serif;
    position: relative;
  }
  .card {
    position: absolute;
    left: 260px;
    width: 680px;
    height: 388px;
    background: linear-gradient(160deg, var(--card-black-2), var(--card-black));
    box-shadow: 0 14px 30px rgba(0,0,0,.35);
    overflow: hidden;
  }
  .card--front { top: 40px; }
  .card--back { top: 472px; }
  .page-curl { position: absolute; right: 0; bottom: 0; width: 170px; height: 170px; }
  .brand {
    position: absolute;
    left: 0; right: 0;
    display: flex; align-items: center; justify-content: center; gap: 12px;
    color: var(--silver);
    font-weight: 700;
    font-size: 40px;
    letter-spacing: 1px;
  }
  .brand__square { width: 22px; height: 22px; background: var(--silver); }
  .card--front .brand { top: 62px; }
  .card--back .brand { top: 38px; }
  .silver-text {
    color: var(--silver);
    text-shadow: 0 0 1px var(--silver-edge), 1px 1px 0 #2b4f6e, 0 2px 3px rgba(0,0,0,.6);
  }
  .tagline {
    position: absolute;
    top: 168px; left: 120px;
    font-family: "PT Sans Narrow", Arial, sans-serif;
    font-size: 33px;
    text-transform: uppercase;
    letter-spacing: .5px;
  }
  .person {
    position: absolute;
    top: 222px; right: 180px;
    text-align: right;
    color: var(--name-blue);
    font-weight: 700;
  }
  .person__name { font-size: 25px; }
  .person__role { font-size: 15px; margin-top: 8px; }
  .website {
    position: absolute;
    top: 140px; left: 0; right: 0;
    text-align: center;
    font-size: 44px;
    font-weight: 700;
    font-style: italic;
    letter-spacing: 1px;
  }
  .contacts {
    position: absolute;
    top: 232px; left: 70px;
    display: flex; gap: 48px;
    font-size: 27px; font-weight: 700; font-style: italic;
  }
  .contact { display: flex; align-items: center; gap: 10px; }
  .contact svg { width: 22px; height: 26px; }
</style>
</head>
<body>

<section class="card card--front" aria-label="Card front">
  <div class="brand"><span class="brand__square"></span>Brightvale</div>
  <p class="tagline silver-text">Commerce Advancing Methods</p>
  <div class="person">
    <p class="person__name">Martin Coles</p>
    <p class="person__role">Senior Partner</p>
  </div>
  <svg class="page-curl" viewBox="0 0 170 170" aria-hidden="true">
    <path d="M170 40 L170 170 L40 170 Z" fill="var(--accent-blue)"/>
    <path d="M170 40 C120 70 80 110 40 170 C70 120 60 90 110 70 Z" fill="var(--accent-blue-dark)" opacity=".7"/>
  </svg>
</section>

<section class="card card--back" aria-label="Card back">
  <div class="brand"><span class="brand__square"></span>Brightvale</div>
  <p class="website silver-text">www.brightvale.example</p>
  <div class="contacts silver-text">
    <span class="contact">
      <svg viewBox="0 0 22 26" aria-hidden="true"><rect x="4" y="1" width="14" height="24" rx="2" fill="none" stroke="var(--silver)" stroke-width="2.5"/><circle cx="11" cy="21" r="1.5" fill="var(--silver)"/></svg>
      1 519 555 0172
    </span>
    <span class="contact">
      <svg viewBox="0 0 22 26" aria-hidden="true"><path d="M6 3 C2 8 2 18 6 23 L10 20 C8 16 8 10 10 6 Z" fill="var(--silver)"/></svg>
      1 877 555 0143
    </span>
  </div>
  <svg class="page-curl" viewBox="0 0 170 170" aria-hidden="true">
    <path d="M170 40 L170 170 L40 170 Z" fill="var(--accent-blue)"/>
    <path d="M170 40 C120 70 80 110 40 170 C70 120 60 90 110 70 Z" fill="var(--accent-blue-dark)" opacity=".7"/>
  </svg>
</section>

</body>
</html>
```